Verdant Ledger - Paid Surveys publisher portal

• Homepage
• Blank Sub Page (Where content goes in between the header/footer)
• Publisher Application Page, complete with Form
• Survey Wall page

Sites that are in a similar vertical that have interesting designs:
rovabin.com
quillmarsh.com
dovek.com
tarn.io

This is a business-to-business site, and needs to have this type of feel to it. Focus on generating revenue, offer completion, paid surveys is the market.

Format: HTML/CSS

Link to current version of application, and form:
https://gridwaveform.brokelqest.com
https://gridwaveform.brokelqest.com/apply
https://gridwaveform.brokelqest.com/panel/4/morvath_user

Please note that we are changing the brand of this project, the name will be determined shortly but everything else remains. It will likely be Verdant Ledger instead of GridWaveform. We will confirm.

Industry/Entity Type

Market Research

Coding

Coded - Design and coding required

Number of Pages Required

4 page

Font styles to use
Sans Serif

Colors

Designer to choose colors to be used in the design.

```html
<!DOCTYPE html>
<html lang="en">
<head>
<meta charset="utf-8">
<title>Verdant Ledger – Survey</title>
<link href="https://fonts.googleapis.com/css2?family=Roboto:wght@300;400;500;700&family=Roboto+Condensed:wght@400;700&display=swap" rel="stylesheet">
<style>
:root{
  --ink:#111;
  --header-bg:#0b0b0b;
  --footer-bg:#262626;
  --brand-blue:#1b3a94;
  --offer-blue:#1a3a96;
  --offer-green:#2f9656;
  --button-dark:#2f2f2f;
  --muted:#8a8a8a;
  --line:#e2e2e2;
  --white:#fff;
  --accent:#2a5bd7;
}
*{box-sizing:border-box;margin:0;padding:0}
html,body{width:1200px;height:1085px;overflow:hidden;background:var(--white);font-family:'Roboto',sans-serif;color:var(--ink)}
.page{position:relative;width:1200px;height:1085px}

.site-header{position:absolute;left:0;top:0;width:1200px;height:86px;background:var(--header-bg)}
.brand{position:absolute;left:178px;top:17px;display:flex;align-items:center;gap:10px}
.brand-mark{width:52px;height:52px;border-radius:50%;background:var(--brand-blue)}
.brand-name{font-family:'Roboto Condensed',sans-serif;font-weight:700;font-size:19px;line-height:20px;color:var(--white);text-transform:uppercase;width:100px}
.main-nav{position:absolute;left:465px;top:0;height:86px;display:flex;gap:27px;font-family:'Roboto Condensed',sans-serif;font-weight:700;font-size:12px;color:var(--white);letter-spacing:.2px}
.main-nav a{position:relative;display:flex;align-items:center;height:86px;color:inherit;text-decoration:none}
.main-nav a.is-active::after{content:"";position:absolute;left:0;right:0;bottom:2px;height:3px;background:var(--white)}
.caret{margin-left:5px;width:7px;height:5px}
.account{position:absolute;left:884px;top:33px;display:flex;align-items:center;gap:7px;font-family:'Roboto Condensed',sans-serif;font-size:12.5px;color:var(--white)}
.search{position:absolute;left:1013px;top:33px}

.hero{position:absolute;left:0;top:86px;width:1200px;height:188px;background:linear-gradient(90deg,#3e3e3e 0%,#575757 40%,#4a4a4a 70%,#3a3a3a 100%)}
.hero-photo{position:absolute;inset:0;background:radial-gradient(ellipse at 45% 55%,rgba(140,140,140,.45),rgba(30,30,30,.1) 70%)}
.hero-title{position:absolute;left:0;right:0;top:72px;text-align:center;color:var(--white);font-weight:700;font-size:32px;letter-spacing:.3px}

.section-title{position:absolute;left:0;right:0;top:318px;text-align:center;font-weight:300;font-size:36px;letter-spacing:.3px;color:#1a1a1a}

.promo-text{position:absolute;font-weight:300;font-size:29px;line-height:38px;color:#1a1a1a}
.btn-dark{position:absolute;display:flex;align-items:center;justify-content:center;background:var(--button-dark);color:var(--white);font-family:'Roboto',sans-serif;font-weight:500;font-size:14px;letter-spacing:1.2px;text-transform:uppercase}

.offer{position:absolute;width:123px;height:123px;background:var(--white);border:1px solid var(--line);box-shadow:0 1px 2px rgba(0,0,0,.05)}
.offer-top{height:72px;background:var(--offer-blue);color:var(--white);text-align:center}
.offer.is-green .offer-top{background:var(--offer-green)}
.offer-value{display:block;padding-top:8px;font-weight:300;font-size:31px;line-height:33px}
.offer-unit{display:block;font-weight:500;font-size:13px;line-height:16px}
.offer-badge{position:absolute;left:30px;top:63px;width:62px;height:28px;background:var(--white);font-weight:700;font-size:11px;display:flex;align-items:center;justify-content:center;box-shadow:0 1px 2px rgba(0,0,0,.12)}
.offer-time{position:absolute;left:0;right:0;bottom:11px;text-align:center;font-size:14px;color:#222}

.to-top{position:absolute;left:584px;top:906px;width:32px;height:32px;border-radius:50%;background:#222;display:flex;align-items:center;justify-content:center}
.site-footer{position:absolute;left:0;top:922px;width:1200px;height:163px;background:var(--footer-bg);text-align:center;font-family:'Roboto Condensed',sans-serif;color:var(--muted)}
.footer-links{position:absolute;left:0;right:0;top:37px;font-size:12px}
.social{position:absolute;left:583px;top:78px;display:flex;gap:13px}
.social span{width:11px;height:11px;border-radius:50%;background:var(--white)}
.copyright{position:absolute;left:0;right:0;top:117px;font-size:12px}
</style>
</head>
<body>
<div class="page">
  <header class="site-header">
    <div class="brand"><span class="brand-mark"></span><span class="brand-name">Verdant Ledger</span></div>
    <nav class="main-nav">
      <a href="#">HOME<svg class="caret" viewBox="0 0 7 5"><path d="M.5 .5 3.5 3.5 6.5 .5" fill="none" stroke="#fff" stroke-width="1.3"/></svg></a>
      <a href="#">PUBLISHER APPLICATION</a>
      <a href="#" class="is-active">SURVEY</a>
    </nav>
    <div class="account">
      <svg width="11" height="12" viewBox="0 0 11 12"><circle cx="5.5" cy="3.2" r="3" fill="#fff"/><path d="M0 12c0-4 2.5-5.5 5.5-5.5S11 8 11 12z" fill="#fff"/></svg>
      Login / Signup
      <svg class="caret" viewBox="0 0 7 5"><path d="M.5 .5 3.5 3.5 6.5 .5" fill="none" stroke="#fff" stroke-width="1.3"/></svg>
    </div>
    <svg class="search" width="13" height="13" viewBox="0 0 13 13"><circle cx="5.3" cy="5.3" r="4" fill="none" stroke="#fff" stroke-width="2"/><path d="M8.3 8.3 12 12" stroke="#fff" stroke-width="2.2"/></svg>
  </header>

  <section class="hero">
    <div class="hero-photo" role="img" aria-label="Hands holding a tablet showing a line chart, darkened"></div>
    <h1 class="hero-title">Earn Points by Completing Any of The Offers Below</h1>
  </section>

  <h2 class="section-title">Choose A Survey and Start Earning</h2>

  <p class="promo-text" style="left:203px;top:460px">Points awarded upon<br>New Profile Completion</p>
  <a class="btn-dark" style="left:207px;top:560px;width:123px;height:41px">Learn More</a>
  <p class="promo-text" style="left:209px;top:675px">Created profile with us<br>before?</p>
  <a class="btn-dark" style="left:207px;top:763px;width:196px;height:41px">Import Your Profile</a>

  <div class="offer" style="left:611px;top:422px"><div class="offer-top"><span class="offer-value">101</span><span class="offer-unit">Coin</span></div><span class="offer-badge">HOT!</span><span class="offer-time">1 min</span></div>
  <div class="offer" style="left:758px;top:422px"><div class="offer-top"><span class="offer-value">65</span><span class="offer-unit">Coin</span></div><span class="offer-badge">HOT!</span><span class="offer-time">9 min</span></div>
  <div class="offer" style="left:904px;top:422px"><div class="offer-top"><span class="offer-value">202</span><span class="offer-unit">Coin</span></div><span class="offer-badge">HOT!</span><span class="offer-time">10 min</span></div>

  <div class="offer" style="left:611px;top:567px"><div class="offer-top"><span class="offer-value">18</span><span class="offer-unit">Coin</span></div><span class="offer-badge">HOT!</span><span class="offer-time">2 min</span></div>
  <div class="offer" style="left:758px;top:567px"><div class="offer-top"><span class="offer-value">278</span><span class="offer-unit">Coin</span></div><span class="offer-badge">HOT!</span><span class="offer-time">12 min</span></div>
  <div class="offer is-green" style="left:904px;top:567px"><div class="offer-top"><span class="offer-value">15</span><span class="offer-unit">Coin</span></div><span class="offer-time">1 min</span></div>

  <div class="offer" style="left:611px;top:716px"><div class="offer-top"><span class="offer-value">239</span><span class="offer-unit">Coin</span></div><span class="offer-badge">HOT!</span><span class="offer-time">13 min</span></div>
  <div class="offer" style="left:758px;top:716px"><div class="offer-top"><span class="offer-value">105</span><span class="offer-unit">Coin</span></div><span class="offer-badge">HOT!</span><span class="offer-time">13 min</span></div>
  <div class="offer" style="left:904px;top:716px"><div class="offer-top"><span class="offer-value">88</span><span class="offer-unit">Coin</span></div><span class="offer-badge">HOT!</span><span class="offer-time">6 min</span></div>

  <footer class="site-footer">
    <p class="footer-links">Home | Publisher | Survey</p>
    <div class="social"><span></span><span></span></div>
    <p class="copyright">©Copyright information here</p>
  </footer>
  <a class="to-top" href="#"><svg width="12" height="8" viewBox="0 0 12 8"><path d="M1 7 6 2l5 5" fill="none" stroke="#fff" stroke-width="1.8"/></svg></a>
</div>
</body>
</html>
```